KAJU Freightways #ALLKAJU Business Cards & Letterhead

I am looking to business cards designed for our organization. We are currently undergoing a small re-branding that is taking place. Our organization is called KAJU Freightways and we are headquartered in Phoenix, AZ. We primarily provide transportation and logistics services to the Marlow Parcel Bureau who is our largest customer. I would like to see a design that incorporates name, title, contact info, website, and address (this will be different depending on the employee). I would also like to see some color on the business card using our logo colors or a variation. I would like our logo on the back of the business card with the website displayed. The final design should communicate that we are a next generation transportation operate that focuses on being driver-first, customer-centric, innovative, and sustainable.We would also like our #ALLKAJU catch phrase incorporated as well.

Target Market(s)

Transportation & Logistics

Industry/Entity Type

Trucking Company

Contact Information for Business Card

-First and Last Name
-Position Title
-Contact Phone
-Contact Email
-Physical Address

Font styles to use
Serif

Colors

Designer to choose colors to be used in the design.

Requirements
Must have
• -KAJU logo prominently displayed
• -#ALLKAJU catch phrase used
• -Some amount of color, design gradient, etc.
• -Logo on the back with website listed (https://www.kajufreightco.example)

```html
<!DOCTYPE html>
<html lang="en">
<head>
<meta charset="utf-8">
<title>KAJU Freightways – Business Cards &amp; Letterhead</title>
<link href="https://fonts.googleapis.com/css2?family=Roboto:wght@400;500;700;900&family=Roboto+Condensed:ital,wght@1,500&display=swap" rel="stylesheet">
<style>
  :root {
    --stage: #999999;
    --paper: #ffffff;
    --ink-dark: #083a46;
    --brand-green: #7cba3d;
    --text-grey: #6b6b6b;
    --rule-grey: #b5b5b5;
    --brand-gradient: linear-gradient(90deg, #063a48 0%, #2c5a4f 35%, #5d9548 70%, #7cba3d 100%);
  }
  * { box-sizing: border-box; margin: 0; padding: 0; }
  html, body { width: 1200px; height: 763px; overflow: hidden; }
  body {
    position: relative;
    background: var(--stage);
    font-family: "Roboto", Arial, sans-serif;
    color: var(--text-grey);
  }

  .card {
    position: absolute;
    left: 91px;
    width: 399px;
    height: 234px;
    border-radius: 9px;
    overflow: hidden;
    border: 1px solid #8a8a8a;
  }
  .card-front { top: 134px; background: var(--paper); }
  .card-back { top: 390px; background: var(--brand-gradient); }

  .wordmark {
    position: absolute;
    display: flex;
    align-items: center;
    gap: 6px;
    font-weight: 900;
    color: var(--ink-dark);
    letter-spacing: 1px;
    line-height: 1;
    transform: translateX(-50%);
    white-space: nowrap;
  }
  .wordmark .mark-dot {
    border-radius: 50%;
    background: var(--brand-green);
    flex: none;
  }
  .tagline {
    position: absolute;
    font-family: "Roboto Condensed", "Arial Narrow", sans-serif;
    font-style: italic;
    font-weight: 500;
    color: var(--brand-green);
    white-space: nowrap;
    transform: translateX(-50%);
  }

  .card-front .wordmark { left: 110px; top: 95px; font-size: 30px; }
  .card-front .wordmark .mark-dot { width: 12px; height: 12px; }
  .card-front .tagline { left: 110px; top: 154px; font-size: 11px; }

  .card-divider {
    position: absolute;
    left: 199px; top: 66px;
    width: 1px; height: 102px;
    background: var(--rule-grey);
  }
  .card-details { position: absolute; left: 215px; top: 65px; }
  .person-name { font-size: 13px; font-weight: 700; color: var(--ink-dark); letter-spacing: .3px; line-height: 1.1; }
  .person-title { font-size: 9.5px; color: var(--brand-green); margin-top: 1px; }
  .address { font-size: 9.5px; line-height: 12px; margin-top: 8px; }
  .contact-list { list-style: none; margin-top: 7px; font-size: 9.5px; line-height: 13px; }
  .contact-list li { display: flex; align-items: center; gap: 3px; }
  .contact-list svg { width: 8px; height: 8px; flex: none; }

  .hashtag-band {
    position: absolute;
    left: 0; right: 0;
    background: var(--brand-gradient);
    color: #ffffff;
    font-weight: 700;
    text-align: center;
    letter-spacing: .3px;
  }
  .card-front .hashtag-band { top: 202px; height: 20px; line-height: 20px; font-size: 9.5px; }

  .card-back .wordmark { left: 200px; top: 100px; font-size: 36px; color: #ffffff; }
  .card-back .wordmark .mark-dot { width: 14px; height: 14px; background: #ffffff; }
  .card-back .site {
    position: absolute; left: 0; right: 0; top: 207px;
    text-align: center; color: #ffffff; font-size: 11px;
  }

  .letterhead {
    position: absolute;
    left: 523px; top: 17px;
    width: 570px; height: 726px;
    background: var(--paper);
  }
  .letterhead .wordmark { left: 85px; top: 49px; font-size: 22px; }
  .letterhead .wordmark .mark-dot { width: 8px; height: 8px; }
  .letterhead .tagline { left: 85px; top: 88px; font-size: 6.5px; }
  .letterhead-contact { position: absolute; left: 406px; top: 35px; font-size: 8px; line-height: 9.5px; }
  .letterhead-contact .contact-list { margin-top: 6px; font-size: 8px; line-height: 11px; }
  .letterhead-contact .contact-list svg { width: 6.5px; height: 6.5px; }
  .letterhead .hashtag-band { top: 686px; height: 27px; line-height: 27px; font-size: 10.5px; }
</style>
</head>
<body>

<svg width="0" height="0" style="position:absolute" aria-hidden="true">
  <defs>
    <symbol id="icon-phone" viewBox="0 0 10 10"><path fill="#7cba3d" d="M2 0.5 L3.6 2.6 L2.8 3.6 C3.4 5 4.8 6.4 6.3 7.1 L7.3 6.3 L9.5 8 L8.4 9.5 C4.5 9.2 0.7 5.4 0.5 1.6 Z"/></symbol>
    <symbol id="icon-mail" viewBox="0 0 10 10"><rect x="0.5" y="2" width="9" height="6.5" fill="#7cba3d"/><path d="M0.8 2.3 L5 5.8 L9.2 2.3" fill="none" stroke="#fff" stroke-width="0.9"/></symbol>
    <symbol id="icon-globe" viewBox="0 0 10 10"><g fill="none" stroke="#7cba3d" stroke-width="0.9"><circle cx="5" cy="5" r="4.4"/><ellipse cx="5" cy="5" rx="2" ry="4.4"/><path d="M0.6 5 H9.4 M1.3 2.8 H8.7 M1.3 7.2 H8.7"/></g></symbol>
  </defs>
</svg>

<section class="card card-front" aria-label="Business card front">
  <div class="wordmark"><span class="mark-dot"></span>KAJU</div>
  <div class="tagline">Transportation and Logistics Services</div>
  <div class="card-divider"></div>
  <div class="card-details">
    <p class="person-name">RHEA CALDER</p>
    <p class="person-title">President</p>
    <p class="address">4120 North Saguaro Ridge Road<br>Phoenix, AZ 85001</p>
    <ul class="contact-list">
      <li><svg><use href="#icon-phone"/></svg>555-014-2290</li>
      <li><svg><use href="#icon-mail"/></svg>info@kajufreightco.example</li>
      <li><svg><use href="#icon-globe"/></svg>www.kajufreightco.example</li>
    </ul>
  </div>
  <div class="hashtag-band">#ALLKAJU</div>
</section>

<section class="card card-back" aria-label="Business card back">
  <div class="wordmark"><span class="mark-dot"></span>KAJU</div>
  <p class="site">www.kajufreightco.example</p>
</section>

<section class="letterhead" aria-label="Letterhead">
  <div class="wordmark"><span class="mark-dot"></span>KAJU</div>
  <div class="tagline">Transportation and Logistics Services</div>
  <div class="letterhead-contact">
    <p>4120 North Saguaro Ridge Road<br>Phoenix, AZ 85001</p>
    <ul class="contact-list">
      <li><svg><use href="#icon-phone"/></svg>555-014-2290</li>
      <li><svg><use href="#icon-mail"/></svg>info@kajufreightco.example</li>
      <li><svg><use href="#icon-globe"/></svg>www.kajufreightco.example</li>
    </ul>
  </div>
  <div class="hashtag-band">#ALLKAJU</div>
</section>

</body>
</html>
```